Corvane Paintless Dent Removal

Our company works on vehicles removing dents using a highly skilled trade which the metal is massaged out with special tools without disturbing the original paint, hence paintless dent removal. Besides keeping the paint and metal original its also very environmentally friendly since no paint or toxic fillers are used. Also we we are one of the most experienced companies in the business with 25 years

Target Market(s)

Retail Automobile consumers, Auto Dealerships and Auto Body Shops

Industry/Entity Type

Auto Repair

Contact Information for Business Card

Dale Hollister
PO Box 518 Brookmere, NY 11962
631-555-0148
corvanepdr@mailbox-example.com
website corvanepdr.example
youtube corvane paintless dent removal
25 years of experience removing Dents, Dings and Hail Damage

Font styles to use
Serif
Sans Serif

Colors

Designer to choose colors to be used in the design.

Requirements
Must have
• I do like things that are simple but classy and somewhat bold, also I like my logo so that should be somewhat important

```html
<!DOCTYPE html>
<html lang="en">
<head>
<meta charset="utf-8">
<title>Corvane Paintless Dent Removal – Business Card</title>
<link href="https://fonts.googleapis.com/css2?family=Roboto:wght@400;500;700;900&display=swap" rel="stylesheet">
<style>
  :root {
    --navy: #13254a;
    --green: #7dc242;
    --card-light: #f2f2f2;
    --backdrop: #c4c4c4;
    --text-dark: #1c2540;
  }
  * { margin: 0; padding: 0; box-sizing: border-box; }
  html, body { width: 1200px; height: 576px; overflow: hidden; }
  body {
    background: var(--backdrop);
    font-family: "Roboto", Arial, sans-serif;
    position: relative;
  }
  .card {
    position: absolute;
    top: 138px;
    width: 484px;
    height: 294px;
    border-radius: 14px;
    overflow: hidden;
  }
  .card-front { left: 82px; background: var(--navy); }
  .card-back { left: 602px; background: var(--card-light); color: var(--text-dark); }

  /* front */
  .front-mark {
    position: absolute;
    top: 112px; left: 0; width: 100%;
    text-align: center;
    color: #ffffff;
    font-weight: 900;
    font-size: 25px;
    letter-spacing: 0.2px;
  }
  .front-web {
    position: absolute;
    top: 262px; left: 0; width: 100%;
    display: flex; align-items: center; justify-content: center; gap: 16px;
    font-size: 12.5px; color: #e6e9ef; letter-spacing: 0.6px;
  }
  .front-web .rule { width: 92px; height: 1.5px; background: var(--green); }
  .front-web .accent { color: var(--green); }

  /* back */
  .back-mark {
    position: absolute; top: 30px; left: 23px;
    color: var(--navy);
    font-weight: 900;
    font-size: 22px;
    line-height: 1.05;
  }
  .back-circle {
    position: absolute;
    top: 56px; left: 330px;
    width: 230px; height: 230px;
    border-radius: 50%;
    background: var(--navy);
  }
  .person { position: absolute; top: 136px; left: 23px; }
  .person-name { font-size: 20px; font-weight: 700; color: var(--navy); }
  .person-title { font-size: 11.5px; margin-top: 3px; }
  .address { position: absolute; top: 186px; left: 23px; font-size: 12.5px; line-height: 16px; }
  .contacts { position: absolute; top: 226px; left: 23px; list-style: none; font-size: 12.5px; }
  .contacts li { display: flex; align-items: center; gap: 10px; height: 17px; }
  .contacts svg { width: 11px; height: 11px; fill: var(--green); flex: none; }
</style>
</head>
<body>
  <section class="card card-front">
    <div class="front-mark">Corvane Paintless Dent Removal</div>
    <div class="front-web">
      <span class="rule"></span>
      <span>www.<span class="accent">corvanepdr</span>.example</span>
      <span class="rule"></span>
    </div>
  </section>

  <section class="card card-back">
    <div class="back-mark">CORVANE<br>Paintless Dent Removal</div>
    <div class="back-circle"></div>
    <div class="person">
      <div class="person-name">Dale Hollister</div>
      <div class="person-title">Managing Director</div>
    </div>
    <div class="address">PO Box 518 Brookmere,<br>NY 11962</div>
    <ul class="contacts">
      <li>
        <svg viewBox="0 0 12 12" aria-hidden="true"><path d="M1 4c0-2 1-3 5-3s5 1 5 3H8.5V3h-5v1zM2.5 5.5h7L11 11H1z"/></svg>
        631-555-0148
      </li>
      <li>
        <svg viewBox="0 0 12 12" aria-hidden="true"><path d="M0 2h12v8H0zM1 3l5 3.5L11 3v-.2H1z" fill-rule="evenodd"/></svg>
        corvanepdr@mailbox-example.com
      </li>
      <li>
        <svg viewBox="0 0 12 12" aria-hidden="true"><circle cx="6" cy="6" r="5.5"/><path d="M0.5 6h11M6 0.5v11M2 3h8M2 9h8" stroke="#f2f2f2" stroke-width="0.8" fill="none"/></svg>
        www.corvanepdr.example
      </li>
    </ul>
  </section>
</body>
</html>
```